Kindle Your Clients Book Cover

A book main title will be, "Kindle Your Clients"
The subtext will be, "Win new markets with a story that burns"
Would like it to blend with my web site brand. You can find it here: www.kindleyourclients.example

Audience is business and revenue leaders for small, medium and large businesses. They have a new solution, or want to enter a new market, and they need to "inspire their buyers" meaning getting the buyers to want to change enough to overcome their status quo bias. They need a story that sizzles to do this.

```html
<!DOCTYPE html>
<html lang="en">
<head>
<meta charset="utf-8">
<title>Kindle Your Clients — Book Cover</title>
<link rel="stylesheet" href="https://fonts.googleapis.com/css2?family=Antonio:wght@700&family=Bebas+Neue&family=Montserrat:wght@700&display=swap">
<style>
  :root {
    --teal: #62cabd;
    --teal-deep: #2a9e90;
    --teal-mid: #46b5a7;
    --ink: #05232a;
    --tm: #3a4a55;
    --white: #ffffff;
  }
  * { margin: 0; padding: 0; box-sizing: border-box; }
  html, body { width: 768px; height: 1200px; overflow: hidden; background: var(--teal); }
  .cover { position: relative; width: 768px; height: 1200px; background: var(--teal); overflow: hidden; }
  .cover-art { position: absolute; inset: 0; }
  .title-main { font-family: "Antonio", "Oswald", sans-serif; font-weight: 700; fill: var(--white); }
  .title-sub { font-family: "Bebas Neue", "Oswald", sans-serif; fill: var(--ink); }
  .trademark { font-family: "Montserrat", sans-serif; font-weight: 700; fill: var(--tm); }
  .tagline { font-family: "Bebas Neue", "Oswald", sans-serif; fill: var(--ink); }
  .author { font-family: "Montserrat", "Helvetica", sans-serif; font-weight: 700; fill: var(--white); }
</style>
</head>
<body>
<main class="cover">
  <svg class="cover-art" width="768" height="1200" viewBox="0 0 768 1200" xmlns="http://www.w3.org/2000/svg">
    <defs>
      <linearGradient id="towers" x1="0" y1="0" x2="0.3" y2="1">
        <stop offset="0" stop-color="var(--teal)"/>
        <stop offset="0.35" stop-color="var(--teal-mid)"/>
        <stop offset="1" stop-color="var(--teal-deep)"/>
      </linearGradient>
    </defs>

    <rect class="background" width="768" height="1200" fill="var(--teal)"/>

    <rect class="skyline-photo" x="0" y="600" width="768" height="600" fill="url(#towers)" role="img" aria-label="Photo looking up at tall residential towers, tinted teal"/>

    <text class="title-main" x="63" y="357" font-size="326" textLength="642" lengthAdjust="spacingAndGlyphs">KINDLE</text>

    <text class="title-sub" x="63" y="499" font-size="119" textLength="630" lengthAdjust="spacingAndGlyphs">YOUR CLIENTS</text>
    <text class="trademark" x="694" y="392" font-size="24">™</text>

    <rect class="tagline-band" x="0" y="600" width="768" height="73" fill="var(--white)"/>
    <rect class="tagline-marker" x="33" y="628" width="16" height="16" fill="var(--teal-deep)"/>
    <text class="tagline" x="80" y="654" font-size="45" textLength="657" lengthAdjust="spacingAndGlyphs">WIN NEW MARKETS WITH A STORY THAT BURNS</text>

    <text class="author" x="41" y="1167" font-size="66" textLength="709" lengthAdjust="spacing">DALE HARTWELL</text>
  </svg>
</main>
</body>
</html>
```